Pebblebrook Plots - Online-only garden installation company

Online-only garden installation company. Our demographic is middle aged / suburban women, and we anticipate Facebook driving traffic to this website, as well as referrals from garden centers. The website must be very simple in design and function.

All orders will be placed through the website, including size of garden (3 options), location in yard, payment, and scheduling of installation date.

The website should employ a 3 step process:

Step 1: Select garden size. Either an 4' X 4', 8' X 4', or 12' X 4'.

Step 2: Select a location. We would like to use google maps to look up a US address, then "drag and drop" one of the garden sizes from step 1 to the location the customer would like us to install the garden at their home.

Step 3: Pick an installation date and pay. Using an online calendar the customer will pick a date, and then pay for the installation via credit card.

The website will be linked to an email account, PebblebrookPlots@mailvale.com to inform us of orders placed.

Target Market(s)

Our demographic is middle aged / suburban women, and we anticipate Facebook driving traffic to this website, as well as referrals from garden centers.

Industry/Entity Type

Coding

Number of Pages Required

Requirements
Must have
• Scheduling and payment options.

```html
<!DOCTYPE html>
<html lang="en">
<head>
<meta charset="utf-8">
<title>Pebblebrook Plots</title>
<link rel="stylesheet" href="https://fonts.googleapis.com/css2?family=Open+Sans:ital,wght@0,400;0,600;0,700;1,400&family=Roboto+Slab:wght@400;700&display=swap">
<style>
:root{
  --green:#1f8a2c;
  --green-dark:#17701f;
  --green-deep:#0f5c18;
  --orange:#e8611a;
  --ink:#333333;
  --muted:#6b6b6b;
  --line:#d9d9d9;
  --paper:#ffffff;
  --footer:#f6f6f4;
  --wood:#3b2a20;
}
*{box-sizing:border-box;margin:0;padding:0}
html,body{width:1200px;height:3072px;overflow:hidden}
body{position:relative;background:var(--paper);font-family:"Open Sans",Arial,sans-serif;color:var(--ink)}
.abs{position:absolute}
.slab{font-family:"Roboto Slab",Georgia,serif}

/* header */
.topbar{left:0;top:0;width:1200px;height:76px;background:var(--green)}
.navbar{left:0;top:76px;width:1200px;height:72px;background:var(--paper)}
.brand-badge{left:96px;top:-18px;width:164px;height:164px;border-radius:50%;background:var(--paper);display:flex;align-items:center;justify-content:center;text-align:center}
.brand-badge span{font-family:"Roboto Slab",Georgia,serif;font-weight:700;color:var(--green-deep);font-size:19px;line-height:1.15;letter-spacing:.5px;margin-top:40px}
.phone{left:588px;top:20px;color:#fff;font-size:22px;font-weight:700;display:flex;align-items:center;gap:8px}
.pay-btn{left:772px;top:18px;width:102px;height:36px;background:var(--orange);color:#fff;font-size:13px;font-weight:600;display:flex;align-items:center;justify-content:center;gap:6px;border:1px solid #f08a52}
.search{left:891px;top:18px;width:210px;height:36px;border:1px solid #9fd3a6;background:var(--green-dark);color:#fff;font-size:12px;font-weight:600;padding:0 14px;display:flex;align-items:center;justify-content:space-between}
.nav{top:110px;left:0;width:1200px;font-family:"Roboto Slab",Georgia,serif;font-size:13px;color:#333}
.nav span{position:absolute}
.nav .active{color:var(--green)}

/* hero */
.hero{left:0;top:148px;width:1200px;height:560px;background:linear-gradient(160deg,#6b5a44 0%,#4a3a2a 35%,#3d4a26 60%,#2e2417 100%)}
.hero-arrow{top:430px;color:#fff;font-size:28px}
.hero-title{left:690px;top:492px;width:410px;text-align:right;color:#fff;font-family:"Roboto Slab",Georgia,serif;font-size:42px;line-height:46px;letter-spacing:.5px}
.hero-btn{left:862px;top:604px;width:238px;height:42px;background:var(--green);color:#fff;font-family:"Roboto Slab",Georgia,serif;font-weight:700;font-size:14px;display:flex;align-items:center;justify-content:center}
.hero-curve{left:0;top:578px}

/* welcome */
.welcome-h{left:0;top:770px;width:1200px;text-align:center;font-family:"Roboto Slab",Georgia,serif;font-size:34px;color:#333}
.welcome-h em{font-style:normal;color:var(--green)}
.welcome-p{left:210px;top:822px;width:780px;text-align:center;font-size:12.5px;line-height:22px;color:var(--muted)}
.feature-img{width:196px;height:164px}
.feature-h{font-family:"Roboto Slab",Georgia,serif;font-size:18px;color:#333}
.feature-p{width:255px;font-size:12px;line-height:21px;color:var(--muted)}
.outline-btn{width:108px;height:32px;border:1px solid #555;border-radius:3px;font-size:11px;font-weight:600;display:flex;align-items:center;justify-content:center;gap:6px;color:#333}

/* how it works */
.how{left:0;top:1198px;width:1200px;height:530px;background:var(--green)}
.grass-edge{left:0;top:1712px;width:1200px;height:54px;background:linear-gradient(180deg,var(--green) 0%,#3c9a3f 55%,#ffffff 100%)}
.how-h{left:0;top:1252px;width:1200px;text-align:center;color:#fff;font-family:"Roboto Slab",Georgia,serif;font-weight:700;font-size:30px}
.how-rule{left:564px;top:1303px;width:72px;height:2px;background:rgba(255,255,255,.6)}
.tool{width:90px;height:110px;border-radius:10px;background:linear-gradient(150deg,#c8b94a,#7c8a3a);opacity:.85}
.step-circle{width:120px;height:120px;border-radius:50%;background:#fff}
.step-num{width:120px;text-align:center;color:#fff;font-family:"Roboto Slab",Georgia,serif;font-size:14px;line-height:17px}
.step-h{width:360px;text-align:center;color:#fff;font-family:"Roboto Slab",Georgia,serif;font-size:18px}
.step-p{width:320px;text-align:center;color:#e8f3e8;font-size:12px;line-height:21px}
.start-btn{left:526px;top:1628px;width:148px;height:36px;background:var(--orange);color:#fff;font-family:"Roboto Slab",Georgia,serif;font-size:17px;display:flex;align-items:center;justify-content:center}

/* news */
.news-h{left:0;top:1846px;width:1200px;text-align:center;font-family:"Roboto Slab",Georgia,serif;font-size:32px;color:#333}
.news-img{width:312px;height:180px}
.date{width:50px;height:62px;background:var(--orange);color:#fff;font-family:"Roboto Slab",Georgia,serif;font-size:14px;line-height:19px;text-align:center;padding-top:12px}
.news-title{font-family:"Roboto Slab",Georgia,serif;font-size:16px;color:#222}
.news-p{width:312px;font-size:11.5px;line-height:20px;color:var(--muted)}
.read-more{font-size:11px;font-weight:700;color:#333;text-decoration:underline}

/* testimonial */
.testimonial{left:0;top:2325px;width:1200px;height:370px;background:linear-gradient(180deg,#4a3426 0%,#3b2a20 60%,#2f3a1c 88%,#4a8f3a 100%)}
.quote-box{left:102px;top:2360px;width:740px;height:134px;border:2px solid rgba(255,255,255,.35);background:rgba(20,14,10,.35);padding:22px 24px;color:#f1ebe4;font-style:italic;font-size:12.5px;line-height:22px}
.avatar{left:828px;top:2432px;width:104px;height:104px;border-radius:50%;background:linear-gradient(150deg,#c89a78,#8a6650);border:4px solid #fff}
.quote-name{left:960px;top:2412px;font-style:italic;font-size:14px;color:#7fc35c}
.quote-role{left:960px;top:2436px;font-style:italic;font-size:14px;color:#fff}

/* footer */
.footer{left:0;top:2695px;width:1200px;height:315px;background:var(--footer)}
.foot-brand{left:102px;top:2800px;width:198px;text-align:center;font-family:"Roboto Slab",Georgia,serif;font-weight:700;font-size:22px;line-height:28px;color:#333}
.foot-h{font-family:"Roboto Slab",Georgia,serif;font-size:18px;color:#333}
.foot-p{font-size:11.5px;line-height:20px;color:var(--muted)}
.email-input{left:385px;top:2855px;width:246px;height:42px;border:1px solid var(--line);background:#fff;font-size:11px;color:#777;padding:0 14px;display:flex;align-items:center}
.sub-btn{left:385px;top:2907px;width:124px;height:34px;background:var(--orange);color:#fff;font-size:12px;font-weight:600;display:flex;align-items:center;justify-content:center}
.contact-row{left:707px;display:flex;gap:14px;font-size:12px;line-height:20px;color:#444}
.contact-row svg{flex:none;margin-top:3px}
.quick{left:995px;top:2805px;font-size:11.5px;line-height:22px;color:#555}
.copy-bar{left:0;top:3010px;width:1200px;height:62px;background:#fff;border-top:1px solid var(--line)}
.copyright{left:98px;top:3035px;font-size:11px;color:#555}
.social{top:3028px;width:28px;height:28px;border:1px solid #333;border-radius:50%}
</style>
</head>
<body>

<!-- header -->
<div class="abs topbar"></div>
<div class="abs navbar"></div>
<div class="abs brand-badge"><span>PEBBLEBROOK<br>PLOTS</span></div>

<div class="abs phone">
  <svg width="18" height="18" viewBox="0 0 24 24" fill="#fff"><path d="M6.6 10.8a15.1 15.1 0 0 0 6.6 6.6l2.2-2.2c.3-.3.7-.4 1-.2 1.1.4 2.3.6 3.6.6.6 0 1 .4 1 1V20c0 .6-.4 1-1 1A17 17 0 0 1 3 4c0-.6.4-1 1-1h3.5c.6 0 1 .4 1 1 0 1.3.2 2.5.6 3.6.1.3 0 .7-.2 1z"/></svg>
  906-555-0182
</div>
<div class="abs pay-btn">
  <svg width="14" height="11" viewBox="0 0 14 11"><rect x="0.5" y="0.5" width="13" height="10" rx="1.5" fill="none" stroke="#fff"/><rect x="0.5" y="3" width="13" height="2" fill="#fff"/></svg>
  PAYMENT
</div>
<div class="abs search">SEARCH
  <svg width="12" height="12" viewBox="0 0 12 12"><circle cx="5" cy="5" r="3.8" fill="none" stroke="#fff" stroke-width="1.6"/><line x1="8" y1="8" x2="11" y2="11" stroke="#fff" stroke-width="1.8"/></svg>
</div>

<nav class="abs nav">
  <span class="active" style="left:473px">HOME</span>
  <span style="left:560px">ABOUT US</span>
  <span style="left:673px">OUR PROCESS</span>
  <span style="left:808px">SCHEDULING</span>
  <span style="left:938px">NEWS</span>
  <span style="left:1022px">CONTACT US</span>
</nav>

<!-- hero -->
<div class="abs hero" role="img" aria-label="Photo of hands planting lettuce seedlings in dark garden soil with a trowel"></div>
<div class="abs hero-arrow" style="left:34px">&#8249;</div>
<div class="abs hero-arrow" style="left:1146px">&#8250;</div>
<div class="abs hero-title">PEBBLEBROOK<br>PLOTS</div>
<div class="abs hero-btn">SCHEDULE AN APPOINTMENT</div>
<svg class="abs hero-curve" width="1200" height="132" viewBox="0 0 1200 132">
  <path d="M0 88 C250 20 520 20 720 80 C880 125 1050 80 1200 20 L1200 132 L0 132 Z" fill="#fff"/>
  <path d="M95 108 C240 60 460 50 690 100 C470 70 260 78 95 108 Z" fill="#1f8a2c"/>
</svg>

<!-- welcome -->
<h1 class="abs welcome-h" style="font-weight:400">WELCOME TO <em>PEBBLEBROOK PLOTS</em></h1>
<p class="abs welcome-p">Pebblebrook Plots builds raised garden beds right in your backyard. Choose a size, show us the spot, and pick a day that suits you. Our crew arrives with the lumber, soil and tools, and leaves you with a finished bed ready for planting. No trips to the store, no heavy lifting, just fresh vegetables and flowers grown at home.</p>

<div class="abs feature-img" style="left:98px;top:942px;background:linear-gradient(180deg,#dfe6d4 0%,#cbbf8f 55%,#6f9a3e 100%)" role="img" aria-label="Illustration of a small wooden garden shed on a lawn"></div>
<h3 class="abs feature-h" style="left:313px;top:940px;font-weight:400">Location in yard</h3>
<p class="abs feature-p" style="left:313px;top:974px">Look up your address on the map, then drag your chosen bed onto the exact spot in your yard where you want it built.</p>
<div class="abs outline-btn" style="left:313px;top:1074px">CLICK HERE &#10148;</div>

<div class="abs feature-img" style="left:633px;top:942px;background:linear-gradient(180deg,#bfe3f2 0%,#e9f4f8 45%,#6cbf45 100%)" role="img" aria-label="Illustration of a wall calendar standing on green grass"></div>
<h3 class="abs feature-h" style="left:848px;top:940px;font-weight:400">Scheduling Of Installation Date</h3>
<p class="abs feature-p" style="left:848px;top:974px">Open the calendar, choose an installation day that works for your family, and pay securely by card in a single step.</p>
<div class="abs outline-btn" style="left:848px;top:1074px">CLICK HERE &#10148;</div>

<!-- how it works -->
<section class="abs how"></section>
<div class="abs grass-edge" role="img" aria-label="Grass blades along the bottom edge of the band"></div>
<h2 class="abs how-h">HOW IT WORKS</h2>
<div class="abs how-rule"></div>
<div class="abs tool" style="left:40px;top:1232px;transform:rotate(-20deg)" role="img" aria-label="Illustration of a garden spade"></div>
<div class="abs tool" style="left:1060px;top:1232px;transform:rotate(20deg)" role="img" aria-label="Illustration of pruning shears"></div>

<div class="abs step-circle" style="left:169px;top:1358px"></div>
<svg class="abs" style="left:203px;top:1388px" width="52" height="44" viewBox="0 0 52 44" fill="none" stroke="#1f8a2c" stroke-width="2.4">
  <rect x="4" y="6" width="44" height="32" rx="2"/><line x1="4" y1="22" x2="48" y2="22"/><line x1="19" y1="6" x2="19" y2="38"/><line x1="33" y1="6" x2="33" y2="38"/>
</svg>
<div class="abs step-num" style="left:169px;top:1460px">Step<br>1</div>
<div class="abs step-h" style="left:49px;top:1500px">Select garden size</div>
<p class="abs step-p" style="left:69px;top:1530px">Pick a 4' x 4', 8' x 4' or 12' x 4' raised bed to suit your space and your plans.</p>

<div class="abs step-circle" style="left:548px;top:1358px"></div>
<svg class="abs" style="left:582px;top:1382px" width="52" height="50" viewBox="0 0 52 50" fill="none" stroke="#1f8a2c" stroke-width="2.4">
  <path d="M18 36 C8 24 6 19 6 15 a12 12 0 0 1 24 0 c0 4-2 9-12 21z"/><circle cx="18" cy="15" r="4.5"/>
  <path d="M36 22 c-5-6-6-8-6-10 a6 6 0 0 1 12 0 c0 2-1 4-6 10z"/><path d="M4 44 h44" stroke-dasharray="4 4"/>
</svg>
<div class="abs step-num" style="left:548px;top:1460px">Step<br>2</div>
<div class="abs step-h" style="left:428px;top:1500px">Select a Location</div>
<p class="abs step-p" style="left:448px;top:1530px">Find your address on the map and drag the bed to the place it should go.</p>

<div class="abs step-circle" style="left:911px;top:1358px"></div>
<svg class="abs" style="left:947px;top:1385px" width="48" height="46" viewBox="0 0 48 46" fill="none" stroke="#1f8a2c" stroke-width="2.4">
  <rect x="3" y="7" width="42" height="36" rx="3"/><line x1="3" y1="16" x2="45" y2="16"/><line x1="13" y1="2" x2="13" y2="11"/><line x1="35" y1="2" x2="35" y2="11"/>
  <g fill="#1f8a2c" stroke="none"><rect x="9" y="21" width="6" height="5"/><rect x="21" y="21" width="6" height="5"/><rect x="33" y="21" width="6" height="5"/><rect x="9" y="31" width="6" height="5"/><rect x="21" y="31" width="6" height="5"/></g>
</svg>
<div class="abs step-num" style="left:911px;top:1460px">Step<br>3</div>
<div class="abs step-h" style="left:791px;top:1500px">Pick an installation date &amp; pay</div>
<p class="abs step-p" style="left:811px;top:1530px">Choose a date on the calendar, then pay by credit card and we handle the rest.</p>

<svg class="abs" style="left:378px;top:1410px" width="70" height="34" viewBox="0 0 70 34" fill="none" stroke="#fff" stroke-width="3">
  <path d="M4 24 C22 6 44 6 62 20"/><path d="M52 20 L63 21 L60 10" stroke-linejoin="round"/>
</svg>
<svg class="abs" style="left:756px;top:1440px" width="70" height="34" viewBox="0 0 70 34" fill="none" stroke="#fff" stroke-width="3">
  <path d="M4 26 C24 30 46 22 62 8"/><path d="M52 8 L63 7 L62 18" stroke-linejoin="round"/>
</svg>

<div class="abs start-btn">Get Started</div>

<!-- news -->
<h2 class="abs news-h" style="font-weight:400">NEWS &amp; UPDATES</h2>

<div class="abs news-img" style="left:98px;top:1925px;background:linear-gradient(160deg,#9cb36a,#4d7a2e 60%,#7a5c3e)" role="img" aria-label="Photo of a woman watering plants in a garden centre"></div>
<div class="abs date" style="left:110px;top:1925px">02<br>JUN</div>
<h3 class="abs news-title" style="left:98px;top:2120px;font-weight:400">Sed do eiusmod tempor incididunt</h3>
<p class="abs news-p" style="left:98px;top:2150px">Spring is the best time to plan a new bed. See which vegetables our customers love to start with each year.</p>
<div class="abs read-more" style="left:98px;top:2226px">READ MORE</div>

<div class="abs news-img" style="left:444px;top:1925px;background:linear-gradient(160deg,#7fae4a,#3f7a2a 55%,#b0564a)" role="img" aria-label="Photo of a smiling gardener holding a crate of fresh vegetables"></div>
<div class="abs date" style="left:456px;top:1925px">02<br>JUN</div>
<h3 class="abs news-title" style="left:444px;top:2120px;font-weight:400">Sed do eiusmod tempor incididunt</h3>
<p class="abs news-p" style="left:444px;top:2150px">Meet one of our happy growers and learn how a small raised bed turned into a summer full of fresh harvests.</p>
<div class="abs read-more" style="left:444px;top:2226px">READ MORE</div>

<div class="abs news-img" style="left:790px;top:1925px;background:linear-gradient(170deg,#c9d3d8,#8f7a5e 40%,#5e8a3e)" role="img" aria-label="Photo of raised vegetable beds on a rooftop garden"></div>
<div class="abs date" style="left:802px;top:1925px">02<br>JUN</div>
<h3 class="abs news-title" style="left:790px;top:2120px;font-weight:400">Sed do eiusmod tempor incididunt</h3>
<p class="abs news-p" style="left:790px;top:2150px">A look at our newest installations, from compact patio plots to long beds lining the back fence of a yard.</p>
<div class="abs read-more" style="left:790px;top:2226px">READ MORE</div>

<!-- testimonial -->
<section class="abs testimonial" role="img" aria-label="Wooden fence backdrop with a wheelbarrow and watering cans on grass"></section>
<blockquote class="abs quote-box">The crew showed up on the day I picked and had two beds built before lunch. Ordering took me five minutes on my phone, and by midsummer we were eating our own tomatoes and beans. I have already sent three of my neighbours to Pebblebrook Plots.</blockquote>
<div class="abs avatar" role="img" aria-label="Customer portrait"></div>
<div class="abs quote-name">Mara Ellison</div>
<div class="abs quote-role">Pebblebrook Plots</div>

<!-- footer -->
<footer class="abs footer"></footer>
<div class="abs foot-brand">PEBBLEBROOK<br>PLOTS</div>

<h4 class="abs foot-h" style="left:385px;top:2770px;font-weight:400">SIGN UP FOR NEWSLETTER</h4>
<p class="abs foot-p" style="left:385px;top:2804px;width:240px">Get planting tips and seasonal offers sent straight to your inbox.</p>
<div class="abs email-input">Enter email</div>
<div class="abs sub-btn">SUBSCRIPTION</div>

<h4 class="abs foot-h" style="left:707px;top:2770px;font-weight:400">CONTACT US</h4>
<div class="abs contact-row" style="top:2810px">
  <svg width="12" height="16" viewBox="0 0 12 16"><path d="M6 0a6 6 0 0 0-6 6c0 4.5 6 10 6 10s6-5.5 6-10a6 6 0 0 0-6-6zm0 8.3A2.3 2.3 0 1 1 6 3.7a2.3 2.3 0 0 1 0 4.6z" fill="#444"/></svg>
  <span>Pebblebrook Plots<br>48 Fernwood Lane, Millbrook, NC<br>27500</span>
</div>
<div class="abs contact-row" style="top:2880px">
  <svg width="13" height="13" viewBox="0 0 24 24" fill="#444"><path d="M6.6 10.8a15.1 15.1 0 0 0 6.6 6.6l2.2-2.2c.3-.3.7-.4 1-.2 1.1.4 2.3.6 3.6.6.6 0 1 .4 1 1V20c0 .6-.4 1-1 1A17 17 0 0 1 3 4c0-.6.4-1 1-1h3.5c.6 0 1 .4 1 1 0 1.3.2 2.5.6 3.6.1.3 0 .7-.2 1z"/></svg>
  <span>Phone:&nbsp; 1-800-555-0147</span>
</div>
<div class="abs contact-row" style="top:2914px">
  <svg width="14" height="11" viewBox="0 0 14 11"><rect x="0" y="0" width="14" height="11" rx="1" fill="#444"/><path d="M1 1 L7 6 L13 1" stroke="#fff" fill="none" stroke-width="1.3"/></svg>
  <span>info@pebblebrookplots.com</span>
</div>

<h4 class="abs foot-h" style="left:993px;top:2770px;font-weight:400">QUICK LINKS</h4>
<ul class="abs quick" style="list-style:none">
  <li>Home</li><li>About Us</li><li>Features</li><li>Services</li><li>FAQ</li><li>Contact Us</li>
</ul>

<div class="abs copy-bar"></div>
<div class="abs copyright">&copy;2016 - 2017 Pebblebrook Plots, All Rights Reserved.</div>
<div class="abs social" style="left:986px"></div>
<div class="abs social" style="left:1016px"></div>
<div class="abs social" style="left:1046px"></div>
<div class="abs social" style="left:1076px"></div>

</body>
</html>
```